CoinHarbor.com Site Redesign

We are looking to redesign our CoinHarbor.com site. This site is focused on helping consumers make smart financial decisions. We provide reviews and articles in various categories.

We are looking for a responsive design to run on wordpress. We will also have adsense advertisements on our page and will want some ad spot space. We are thinking of two column design vs. single column.

Here is an example of what our competitors look like:
ShopperBeacon.org (mostly reviews vs. articles)
Homepage - https://www.shopperbeacon.example/
Category Review Listing - https://www.shopperbeacon.example/mortgage-refinance/best-mortgage-refinance
Individual Review - https://www.shopperbeacon.example/mortgage-refinance/c/loan-orchard-mortgage-refinance-review

- I like that the site is extremely clean. I like the fixed header in mobile

PilotGuide
Homepage - https://www.pilotguide.example/
Category Review Listing-https://www.pilotguide.example/auto_insurance/index.php
Individual Review- https://www.pilotguide.example/auto_insurance/drivora_review.php

Articles - https://www.pilotguide.example/blog/2017/11/20/going-on-a-holiday-road-trip-be-prepared-for-these-hazards/

What I Like? I like the two column layout in that it gives room for advertising.
What I Do NOT Like? The top navigation is a little cumbersome and old. Mobile view is not very good. Content seems a bit cluttered.

PennyMoth
Homepage - https://www.pennymoth.example
Category Review Listing - https://www.pennymoth.example/blog/insurance/best-car-insurance-companies/?trk=pm_gn1_4.0
Individual Review- https://www.pennymoth.example/blog/insurance/veloro-insurance-review/

What I Like? very clean. Like the use of white space and focus on bright color call to action buttons.
What I Do NOT Like? In mobile a lot of content is pushed below the fold because of the large image above the fold. Reviews are not well organized.

Target Market(s)

consumers interested in saving money and making smart financial decisions

Industry/Entity Type

Financial

Logo Text

CoinHarbor.com or CoinHarbor

Coding

Coded - Design and coding required

Number of Pages Required

5+ page

Font styles to use
Sans Serif

Colors

Designer to choose colors to be used in the design.

Requirements
Must have
• -responsive design
• -room for ad space in the right column
Nice to have
• -good use of white space
• -clean layouts
Should not have
• -clutter

```html
<!DOCTYPE html>
<html lang="en">
<head>
<meta charset="utf-8">
<title>CoinHarbor.com</title>
<link href="https://fonts.googleapis.com/css2?family=Lato:wght@400;700;900&display=swap" rel="stylesheet">
<style>
:root{
  --navy:#0d3a78;
  --navy-dark:#0a2f66;
  --blue:#1a6fb5;
  --blue-light:#1f86cf;
  --orange:#f39a1e;
  --ink:#222b36;
  --muted:#6a727c;
  --line:#dcdfe3;
  --grey-bg:#eeeff1;
  --white:#ffffff;
}
*{box-sizing:border-box;margin:0;padding:0}
html,body{width:1200px;height:3261px;overflow:hidden}
body{position:relative;font-family:'Lato',sans-serif;color:var(--ink);background:var(--white)}
.abs{position:absolute}
/* header + hero */
.hero{left:0;top:0;width:1200px;height:517px;background:linear-gradient(180deg,#f7f7f8 0%,#e9eaec 100%);border-bottom:1px solid #d6d8db}
.brand{display:flex;align-items:center;gap:8px;font-weight:900;color:var(--navy);font-size:19px}
.brand-mark{width:22px;height:22px;border-radius:50%;background:var(--blue)}
.site-brand{left:117px;top:26px}
.main-nav{left:433px;top:32px;font-size:14px;color:#3b4250}
.main-nav span{position:absolute;white-space:nowrap}
.hero-art{left:590px;top:172px;width:525px;height:232px;background:radial-gradient(ellipse at 45% 55%,#cfe0f1 0%,#e6edf4 55%,rgba(233,234,236,0) 75%);border-bottom:2px solid #4b5563}
.hero-title{left:115px;top:188px;font-size:42px;line-height:44px;font-weight:900;color:var(--navy);z-index:2}
.hero-sub{left:116px;top:280px;font-size:17px;font-weight:900;color:var(--blue);white-space:nowrap;z-index:2}
.hero-note{left:116px;top:322px;font-size:14px;color:#333;z-index:2}
.btn-outline{left:116px;top:358px;width:137px;height:38px;border:2px solid var(--navy);color:var(--navy);font-size:15px;display:flex;align-items:center;justify-content:center}
/* categories */
.section-title{font-size:28px;color:var(--ink);font-weight:400}
.cat-title{left:0;width:1200px;top:556px;text-align:center}
.cat{width:228px;height:175px;background:var(--white);border:1px solid var(--line);box-shadow:0 2px 4px rgba(0,0,0,.08);text-align:center}
.cat svg{position:absolute;left:50%;top:30px;transform:translateX(-50%)}
.cat-label{position:absolute;left:0;right:0;bottom:40px;font-size:15px;font-weight:900;color:var(--blue);line-height:19px}
.cat-label.two{bottom:28px}
/* about band */
.about{left:0;top:1222px;width:1200px;height:426px;background:linear-gradient(120deg,#0b3785 0%,#1663b2 60%,#1b79c6 100%)}
.about-title{left:0;width:1200px;top:1258px;text-align:center;color:var(--white);font-size:31px;font-weight:700}
.about-sub{left:0;width:1200px;top:1302px;text-align:center;color:#dce9f7;font-size:18px}
/* articles */
.art-title{left:117px;top:1686px}
.card{background:var(--white);border:1px solid var(--line);box-shadow:0 1px 3px rgba(0,0,0,.06);padding:16px 18px}
.card-photo{width:100%;height:160px}
.card h3{font-size:15px;font-weight:900;margin-top:12px;line-height:19px;color:#1c232c}
.card p{font-size:12px;color:var(--muted);line-height:16px;margin-top:7px}
.card .more{font-size:12px;color:var(--blue);font-weight:700;margin-top:6px;display:block}
.ad{width:247px}
/* newsletter */
.newsletter{left:0;top:2813px;width:1200px;height:74px;background:var(--navy)}
.nl-text{left:210px;top:2835px;font-size:21px;color:var(--white)}
.nl-input{left:520px;top:2832px;width:373px;height:37px;background:var(--white);font-size:13px;color:#7a818a;display:flex;align-items:center;padding-left:44px}
.nl-btn{left:897px;top:2832px;width:117px;height:37px;background:var(--blue-light);color:var(--white);font-size:15px;font-weight:700;display:flex;align-items:center;justify-content:center}
/* footer */
.footer{left:0;top:2887px;width:1200px;height:310px;background:var(--grey-bg)}
.foot-brand{left:148px;top:2947px}
.social{left:146px;top:3008px;display:flex;gap:14px}
.social span{width:34px;height:34px;border-radius:50%;background:var(--blue-light)}
.foot-head{font-size:19px;font-weight:700;color:var(--navy)}
.foot-list{list-style:none;font-size:13px;color:#4a525c;line-height:26px}
.copy{left:0;width:1200px;top:3210px;text-align:center;font-size:12px;color:#7d848c}
</style>
</head>
<body>

<!-- Hero -->
<div class="abs hero"></div>
<div class="abs brand site-brand"><span class="brand-mark"></span>CoinHarbor.com</div>
<nav class="abs main-nav">
  <span style="left:0">Annuities</span>
  <span style="left:87px">Auto Insurance</span>
  <span style="left:215px">Credit Monitoring</span>
  <span style="left:363px">Debt Management</span>
  <span style="left:506px">Mortgages</span>
  <svg style="position:absolute;left:620px;top:0" width="18" height="18" viewBox="0 0 18 18" fill="none" stroke="#6b7280" stroke-width="2"><circle cx="7.5" cy="7.5" r="5.5"/><path d="M12 12l5 5"/></svg>
</nav>
<div class="abs hero-art" role="img" aria-label="Line illustration of a financial adviser presenting charts, graphs and a city skyline"></div>
<h1 class="abs hero-title">Make Smarter<br>Financial Decisions</h1>
<div class="abs hero-sub">FIND THE BEST FINANCIAL PRODUCTS &amp; SERVICES</div>
<div class="abs hero-note">Disclosure: We receive advertising revenue from some partners.</div>
<div class="abs btn-outline">Learn More</div>

<!-- Categories -->
<h2 class="abs section-title cat-title">I'm looking for Product or Category</h2>

<div class="abs cat" style="left:115px;top:628px">
  <svg width="70" height="64" viewBox="0 0 70 64" fill="none" stroke="#0d3a78" stroke-width="2.5"><circle cx="35" cy="34" r="22"/><path d="M14 14l8-6M56 14l-8-6"/><path d="M40 26c-2-3-10-3-10 2s10 3 10 8-8 5-10 2M35 20v28" stroke="#1a6fb5"/></svg>
  <div class="cat-label">ANNUITIES</div></div>
<div class="abs cat" style="left:363px;top:628px">
  <svg width="76" height="60" viewBox="0 0 76 60" fill="none" stroke="#0d3a78" stroke-width="2.5"><path d="M14 40V28l8-14h32l8 14v12z"/><path d="M20 28h36"/><circle cx="22" cy="34" r="3"/><circle cx="54" cy="34" r="3"/><path d="M18 40v8M58 40v8"/></svg>
  <div class="cat-label">AUTO INSURANCE</div></div>
<div class="abs cat" style="left:609px;top:628px">
  <svg width="70" height="64" viewBox="0 0 70 64" fill="none" stroke="#0d3a78" stroke-width="2.5"><path d="M10 6v50h54"/><path d="M14 44l12-16 10 8 12-18 12 12" stroke="#1a6fb5"/><path d="M54 30h6v-6"/></svg>
  <div class="cat-label">CREDIT MONITORING</div></div>
<div class="abs cat" style="left:854px;top:628px">
  <svg width="76" height="60" viewBox="0 0 76 60" fill="none" stroke="#0d3a78" stroke-width="2.5"><rect x="6" y="12" width="64" height="40" rx="4"/><path d="M6 22h64" stroke-width="5"/><path d="M14 40h20M14 45h12" stroke="#1a6fb5"/></svg>
  <div class="cat-label">CREDIT REPAIR</div></div>

<div class="abs cat" style="left:115px;top:817px">
  <svg width="76" height="64" viewBox="0 0 76 64" fill="none" stroke="#0d3a78" stroke-width="2.5"><rect x="6" y="22" width="64" height="36" rx="3"/><circle cx="38" cy="40" r="11" stroke="#1a6fb5"/><path d="M26 22V8h24v14"/></svg>
  <div class="cat-label">DEBT MANAGEMENT</div></div>
<div class="abs cat" style="left:363px;top:817px">
  <svg width="70" height="64" viewBox="0 0 70 64" fill="none" stroke="#0d3a78" stroke-width="2.5"><path d="M35 6l24 9v16c0 14-10 23-24 28-14-5-24-14-24-28V15z"/><path d="M25 32l7 7 13-14" stroke="#1a6fb5"/></svg>
  <div class="cat-label">IDENTITY THEFT</div></div>
<div class="abs cat" style="left:609px;top:817px">
  <svg width="70" height="64" viewBox="0 0 70 64" fill="none" stroke="#0d3a78" stroke-width="2.5"><path d="M6 30a29 24 0 0 1 58 0z"/><path d="M35 30v22a5 5 0 0 1-10 0" stroke="#1a6fb5"/></svg>
  <div class="cat-label">LIFE INSURANCE</div></div>
<div class="abs cat" style="left:854px;top:817px">
  <svg width="70" height="64" viewBox="0 0 70 64" fill="none" stroke="#0d3a78" stroke-width="2.5"><path d="M10 30L35 8l25 22"/><path d="M16 26v30h38V26"/><rect x="29" y="38" width="12" height="18" stroke="#1a6fb5"/></svg>
  <div class="cat-label">MORTGAGES</div></div>

<div class="abs cat" style="left:115px;top:1004px">
  <svg width="70" height="64" viewBox="0 0 70 64" fill="none" stroke="#0d3a78" stroke-width="2.5"><rect x="10" y="14" width="22" height="40" rx="11"/><path d="M21 14v12M10 28h22"/><path d="M50 8a9 9 0 0 1 9 9c0 7-9 17-9 17s-9-10-9-17a9 9 0 0 1 9-9z" stroke="#1a6fb5"/></svg>
  <div class="cat-label">ONLINE BROKERAGES</div></div>
<div class="abs cat" style="left:363px;top:1004px">
  <svg width="70" height="64" viewBox="0 0 70 64" fill="none" stroke="#0d3a78" stroke-width="2.5"><circle cx="38" cy="16" r="10" stroke="#1a6fb5"/><path d="M33 21l10-10"/><path d="M6 46l14-10h16l8 6h-16M20 52h26l18-14"/></svg>
  <div class="cat-label">PAYDAY LOANS</div></div>
<div class="abs cat" style="left:609px;top:1004px">
  <svg width="70" height="64" viewBox="0 0 70 64" fill="none" stroke="#0d3a78" stroke-width="2.5"><circle cx="35" cy="20" r="13"/><path d="M39 14c-2-2-8-2-8 2s8 2 8 6-6 4-8 2M35 10v20" stroke="#1a6fb5"/><path d="M12 58c2-12 12-18 23-18s21 6 23 18"/></svg>
  <div class="cat-label">PERSONAL FINANCE</div></div>
<div class="abs cat" style="left:854px;top:1004px">
  <svg width="76" height="64" viewBox="0 0 76 64" fill="none" stroke="#0d3a78" stroke-width="2.5"><circle cx="38" cy="14" r="10" stroke="#1a6fb5"/><path d="M6 36l32-12 32 12-32 12z"/><path d="M20 42v10c10 6 26 6 36 0V42M66 37v14"/></svg>
  <div class="cat-label two">STUDENT LOAN<br>CONSOLIDATION</div></div>

<!-- About band -->
<div class="abs about"></div>
<h2 class="abs about-title">What is CoinHarbor.com?</h2>
<div class="abs about-sub">Financial Service Advice and Reviews</div>
<svg class="abs" style="left:220px;top:1342px" width="770" height="280" viewBox="0 0 770 280">
  <g fill="none" stroke-width="24">
    <circle cx="141" cy="138" r="118" stroke="#cfd3d8"/>
    <circle cx="384" cy="138" r="118" stroke="#cfd3d8"/>
    <circle cx="626" cy="138" r="118" stroke="#cfd3d8"/>
    <path d="M23 138A118 118 0 0 1 259 138" stroke="#1a7bbf"/>
    <path d="M266 138A118 118 0 0 0 502 138" stroke="#f39a1e"/>
    <path d="M508 138A118 118 0 0 1 744 138" stroke="#0d3a78"/>
  </g>
  <path d="M245 140h28l-14 18z" fill="#1a7bbf"/>
  <path d="M488 136h28l-14-18z" fill="#f39a1e"/>
  <path d="M730 140h28l-14 18z" fill="#0d3a78"/>
  <g fill="#ffffff"><circle cx="141" cy="138" r="104"/><circle cx="384" cy="138" r="104"/><circle cx="626" cy="138" r="104"/></g>
  <g fill="none" stroke="#1a7bbf" stroke-width="3"><path d="M110 105l14 14 14-18 18 16"/><path d="M130 90l8 8 18-20"/><circle cx="110" cy="105" r="4"/><circle cx="124" cy="119" r="4"/><circle cx="156" cy="117" r="4"/></g>
  <g fill="none" stroke="#f39a1e" stroke-width="3"><path d="M384 76v44M364 84h40M364 84l-10 22h20zM404 84l-10 22h20zM372 122h24"/></g>
  <g fill="none" stroke="#0d3a78" stroke-width="3"><path d="M604 80h44v30h-28l-12 10v-10h-4z"/></g>
  <g fill="#0d3a78"><circle cx="616" cy="95" r="3"/><circle cx="626" cy="95" r="3"/><circle cx="636" cy="95" r="3"/></g>
  <g font-family="Lato,sans-serif" font-size="19" fill="#333" text-anchor="middle">
    <text x="141" y="167">We Analyze &amp;</text><text x="141" y="191">Explain</text>
    <text x="384" y="167">We Test &amp;</text><text x="384" y="191">Compare</text>
    <text x="626" y="167">We Review</text><text x="626" y="191">&amp; Rate</text>
  </g>
</svg>

<!-- Articles -->
<h2 class="abs section-title art-title">Latest Articles</h2>

<article class="abs card" style="left:115px;top:1741px;width:335px;height:313px">
  <div class="card-photo" role="img" aria-label="Photo of hands using a laptop beside a coffee cup" style="background:linear-gradient(135deg,#6b5a4a,#c9b59b)"></div>
  <h3>5 "Easy" Ways Parents Can Save $1000's a Year</h3>
  <p>Parents, let's face it – the high cost of raising children leaves us all needing a little</p>
  <span class="more">READ MORE</span></article>
<article class="abs card" style="left:465px;top:1741px;width:335px;height:313px">
  <div class="card-photo" role="img" aria-label="Photo of a crashed motorcycle lying on a road" style="background:linear-gradient(135deg,#4c5157,#a9aeb3)"></div>
  <h3>Motorcycle Insurance Basics</h3>
  <p>Motorcycle insurance can be quite expensive; it can be the same amount as an auto insurance quote in some cases.</p>
  <span class="more">READ MORE</span></article>

<article class="abs card" style="left:115px;top:2083px;width:335px;height:315px">
  <div class="card-photo" role="img" aria-label="Photo of a man in a suit reviewing a tablet next to a car" style="background:linear-gradient(135deg,#3a4048,#b8bcc2)"></div>
  <h3>How Do I Get Cheap Auto Insurance?</h3>
  <p>Parents, let's face it – the high cost of raising children leaves us all needing a little Vivamus porttitor purus nisi eleifend</p>
  <span class="more">READ MORE</span></article>
<article class="abs card" style="left:465px;top:2083px;width:335px;height:315px">
  <div class="card-photo" role="img" aria-label="Image of a glowing blue stock market chart" style="background:linear-gradient(135deg,#0b2a4a,#1aa5c9)"></div>
  <h3>Morbi diam mauris viverra in gravida</h3>
  <p>Motorcycle insurance can be quite expensive; it can be the same amount as an auto insurance quote in some cases.</p>
  <span class="more">READ MORE</span></article>

<article class="abs card" style="left:115px;top:2422px;width:335px;height:313px">
  <div class="card-photo" role="img" aria-label="Photo of hands reviewing financial charts on a desk with a laptop" style="background:linear-gradient(135deg,#8d99a6,#e3e7ec)"></div>
  <h3>Donec convallis pede veneVivamus porttitor purus nisi eleifen</h3>
  <p>Parents, let's face it – the high cost of raising children leaves us all needing a little</p>
  <span class="more">READ MORE</span></article>
<article class="abs card" style="left:465px;top:2422px;width:335px;height:313px">
  <div class="card-photo" role="img" aria-label="Photo of a smiling businessman in an office meeting room" style="background:linear-gradient(135deg,#2f3d4d,#9aa8b6)"></div>
  <h3>Vivamus porttitor purus</h3>
  <p>Motorcycle insurance can be quite expensive; it can be the same amount as an auto insurance quote in some cases.</p>
  <span class="more">READ MORE</span></article>

<!-- Ad column -->
<div class="abs ad" style="left:833px;top:1741px;height:205px;background:linear-gradient(180deg,#ffffff 0%,#ffffff 14%,#4cae3c 14%,#2f8f2b 100%)" role="img" aria-label="Advertisement for LedgerLeaf accounting software: stay productive on the go, try it free"></div>
<div class="abs ad" style="left:833px;top:1980px;height:205px;background:linear-gradient(180deg,#ffffff 0%,#eef4fb 55%,#1b6fc0 100%)" role="img" aria-label="Advertisement for responsive web design, 50% offer"></div>
<div class="abs ad" style="left:833px;top:2215px;height:205px;background:linear-gradient(160deg,#1d3f86 0%,#10285e 100%)" role="img" aria-label="Advertisement for Northgate Lending mortgage lender, customer rating 4.9 out of 5, apply now"></div>
<div class="abs ad" style="left:833px;top:2446px;height:204px;background:linear-gradient(180deg,#f4f4f4 0%,#e2e4e8 100%)" role="img" aria-label="Advertisement: website not making money? Find out why with this free checklist, download it now"></div>

<!-- Newsletter -->
<div class="abs newsletter"></div>
<div class="abs nl-text">Sign Up for Our Newsletters</div>
<div class="abs nl-input">EMAIL ADDRESS</div>
<svg class="abs" style="left:534px;top:2844px" width="20" height="14" viewBox="0 0 20 14" fill="none" stroke="#8a9099" stroke-width="1.5"><rect x="1" y="1" width="18" height="12"/><path d="M1 1l9 7 9-7"/></svg>
<div class="abs nl-btn">Subscribe</div>

<!-- Footer -->
<footer class="abs footer"></footer>
<div class="abs brand foot-brand"><span class="brand-mark"></span>CoinHarbor.com</div>
<div class="abs social" aria-label="Social links"><span></span><span></span><span></span><span></span><span></span></div>
<div class="abs foot-head" style="left:454px;top:2936px">Our Services</div>
<ul class="abs foot-list" style="left:454px;top:2974px"><li>Annuities</li><li>Auto Insurance</li><li>Credit Monitoring</li><li>Credit Repair</li><li>Debt Management</li></ul>
<ul class="abs foot-list" style="left:643px;top:2974px"><li>Identity Theft</li><li>Life Insurance</li><li>Mortgages</li><li>Online Brokerages</li><li>Payday Loans</li></ul>
<div class="abs foot-head" style="left:852px;top:2936px">Our Company</div>
<ul class="abs foot-list" style="left:856px;top:2974px"><li>Home</li><li>About Us</li><li>Why We Are</li><li>Latest Articles</li><li>Contact Us</li></ul>
<div class="abs copy">© 2017 Company Name &nbsp;All right reserved</div>

</body>
</html>
```